Young, dynamic furniture company needs a new business card design

We require a new business card design for our modern furniture company which supplies furniture and appliances to the property and development market.
Oakridge Interiors has become one of the leading furniture & appliance suppliers to the property market withing London. With over 10 years experience, we have increased our business to supply not only private landlords and managing agents, but also property developers, housing associations and local councils.
We offer not only a complete range of furniture which includes beds, wardrobes, dining sets and sofas, but also a high quality, full delivery and assembly service to help you with all our furnishing needs.

Target Market(s)

Private landlords, estate agents, letting agents, property management companies

Industry/Entity Type

Business

Contact Information for Business Card

Name,
Title,
Address,
Mobile,
Telephone,
Fax, Website, email address

Font styles to use
Sans Serif

Colors
3176b5
0555a3
85abd2
cfdeed

Requirements
Must have
• All the above information for each of our staff, along with our logo

```html
<!DOCTYPE html>
<html lang="en">
<head>
<meta charset="utf-8">
<title>Oakridge Interiors – Business Card</title>
<link href="https://fonts.googleapis.com/css2?family=Roboto:wght@300;400;500;700&display=swap" rel="stylesheet">
<style>
  :root {
    --stage: #2b2c2e;
    --brand-blue: #3176b5;
    --brand-blue-light: #3d86c9;
    --deep-blue: #1f4f9e;
    --stripe-blue: #2f7fcf;
    --pale-blue: #cfdeed;
    --ink: #1d1d1f;
    --white: #ffffff;
  }
  * { box-sizing: border-box; margin: 0; padding: 0; }
  html, body { width: 1200px; height: 950px; overflow: hidden; }
  body {
    background: var(--stage);
    font-family: "Roboto", Arial, sans-serif;
    position: relative;
  }
  .card {
    position: absolute;
    left: 250px;
    width: 700px;
    height: 400px;
    overflow: hidden;
  }
  .card--front { top: 50px; background: linear-gradient(135deg, var(--brand-blue-light), var(--brand-blue)); }
  .card--back { top: 500px; background: var(--white); }

  .front-brand {
    position: absolute; left: 0; right: 0; top: 115px;
    text-align: center; color: var(--white);
  }
  .brand-square {
    display: inline-block; width: 46px; height: 46px;
    background: var(--white); margin-bottom: 18px;
  }
  .brand-name {
    font-size: 26px; font-weight: 400; letter-spacing: 0.5px; text-transform: uppercase;
    white-space: nowrap;
  }
  .brand-tagline {
    font-size: 12px; font-weight: 400; letter-spacing: 0.8px; text-transform: uppercase; margin-top: 3px;
    white-space: nowrap;
  }
  .front-web {
    position: absolute; left: 0; right: 0; bottom: 62px;
    text-align: center; color: var(--white);
    font-size: 15px; font-weight: 300; letter-spacing: 5px;
  }

  .back-shapes { position: absolute; inset: 0; }
  .back-brand {
    position: absolute; left: 40px; top: 130px; color: var(--ink);
  }
  .back-brand .brand-square { background: var(--deep-blue); margin-bottom: 12px; }
  .back-brand .brand-name { font-size: 23px; }
  .back-brand .brand-tagline { font-size: 10px; }

  .contact {
    position: absolute; right: 44px; top: 48px;
    text-align: right; color: var(--white);
  }
  .contact-name { font-size: 22px; font-weight: 700; letter-spacing: 0.5px; }
  .contact-title { font-size: 14px; font-weight: 400; letter-spacing: 1px; margin-bottom: 22px; }
  .contact-list { list-style: none; }
  .contact-list li {
    display: flex; justify-content: flex-end; align-items: center; gap: 9px;
    font-size: 15px; font-weight: 400; line-height: 26px;
    white-space: nowrap;
  }
  .contact-list svg { width: 14px; height: 14px; flex: none; }

  .address {
    position: absolute; right: 44px; bottom: 38px;
    text-align: right; color: var(--white); font-style: normal;
    font-size: 15px; line-height: 22px;
    border-top: 1px solid var(--pale-blue); padding-top: 10px;
  }
</style>
</head>
<body>

<section class="card card--front" aria-label="Card front">
  <div class="front-brand">
    <span class="brand-square"></span>
    <div class="brand-name">Oakridge Interiors</div>
    <div class="brand-tagline">Property Furnishing Specialists</div>
  </div>
  <div class="front-web">www.oakridgeint.com</div>
</section>

<section class="card card--back" aria-label="Card back">
  <svg class="back-shapes" viewBox="0 0 700 400" width="700" height="400" aria-hidden="true">
    <polygon points="450,0 462,0 222,400 210,400" fill="var(--stripe-blue)"/>
    <polygon points="470,0 700,0 700,400 230,400" fill="var(--deep-blue)"/>
  </svg>

  <div class="back-brand">
    <span class="brand-square"></span>
    <div class="brand-name">Oakridge Interiors</div>
    <div class="brand-tagline">Property Furnishing Specialists</div>
  </div>

  <div class="contact">
    <div class="contact-name">MARCUS HALE</div>
    <div class="contact-title">PRESIDENT</div>
    <ul class="contact-list">
      <li>555 0142 7710
        <svg viewBox="0 0 14 14"><path d="M3 1h3l1 3-2 1.5a8 8 0 0 0 3.5 3.5L10 7l3 1v3c0 1-1 2-2 2A11 11 0 0 1 1 3c0-1 1-2 2-2z" fill="#fff"/></svg>
      </li>
      <li>555 0187 4062
        <svg viewBox="0 0 14 14"><rect x="3.5" y="0.5" width="7" height="13" rx="1.5" fill="none" stroke="#fff"/><circle cx="7" cy="11" r="0.9" fill="#fff"/></svg>
      </li>
      <li>555 0193 8195
        <svg viewBox="0 0 14 14"><rect x="3" y="1" width="8" height="4" fill="#fff"/><rect x="1" y="5" width="12" height="5" rx="1" fill="#fff"/><rect x="3" y="9" width="8" height="4" fill="none" stroke="#fff"/></svg>
      </li>
      <li>marcus@oakridgeint.com
        <svg viewBox="0 0 14 14"><rect x="0.5" y="2.5" width="13" height="9" fill="none" stroke="#fff"/><path d="M0.5 2.5 7 8l6.5-5.5" fill="none" stroke="#fff"/></svg>
      </li>
      <li>www.oakridgeint.com
        <svg viewBox="0 0 14 14"><circle cx="7" cy="7" r="6.3" fill="none" stroke="#fff"/><ellipse cx="7" cy="7" rx="2.6" ry="6.3" fill="none" stroke="#fff"/><path d="M0.7 7h12.6" stroke="#fff"/></svg>
      </li>
    </ul>
  </div>

  <address class="address">
    27 Larchmont Road<br>
    Hollis Bay, NY 11042
  </address>
</section>

</body>
</html>
```